Request for Business Card Design

Hi. My name is Marlene, I am looking for a new business card design for my company, Quarrow Signal Instruments, LLC. I really like the design you did for Tarsel Venture and was hoping you could do something similar using our full logo and our mark. I am also open to any raised texture design using our mark. I have attached our full logo, which would need to be somewhere on the card, as well as the mark in both outline and full form, as well as our brand colors / guide. The card does not have to be white, as long as our logo and mark appear. I actually like darker colored business cards more, but am open to all options. If you are interested in working with me, please let me know. We would also take the business card design into letterhead design if you can do that.

```html
<!DOCTYPE html>
<html lang="en">
<head>
<meta charset="utf-8">
<title>Quarrow Signal Instruments — Business Card</title>
<link href="https://fonts.googleapis.com/css2?family=Open+Sans:wght@400;600;700;800&display=swap" rel="stylesheet">
<style>
  :root {
    --backdrop: #222223;
    --card-dark: #3b3c3e;
    --card-blue: #1a9ec8;
    --brand-blue: #1b9fd0;
    --brand-deep: #0f6f8f;
    --ink-light: #f2f4f5;
    --ink-muted: #1e1f21;
  }
  html, body {
    margin: 0;
    width: 1200px;
    height: 780px;
    overflow: hidden;
    background: var(--backdrop);
    font-family: "Open Sans", Arial, sans-serif;
  }
  .canvas {
    width: 1200px;
    height: 780px;
    display: flex;
    align-items: center;
    justify-content: center;
    gap: 44px;
  }
  .card {
    position: relative;
    width: 520px;
    height: 300px;
    border-radius: 3px;
    overflow: hidden;
    box-shadow: 0 18px 40px rgba(0,0,0,0.45);
  }

  /* Back side: contact details */
  .card--back { background: var(--card-dark); }
  .wordmark {
    position: absolute;
    display: flex;
    align-items: center;
    gap: 10px;
  }
  .wordmark__dot {
    width: 30px;
    height: 30px;
    border-radius: 50%;
    background: currentColor;
    flex: none;
  }
  .wordmark__text { line-height: 1; }
  .wordmark__name {
    display: block;
    font-weight: 800;
    letter-spacing: 3px;
    font-size: 26px;
  }
  .wordmark__tag {
    display: block;
    font-weight: 800;
    letter-spacing: 1.2px;
    font-size: 8.5px;
    margin-top: 4px;
  }
  .card--back .wordmark {
    top: 26px;
    left: 28px;
    color: var(--ink-muted);
  }
  .contact {
    position: absolute;
    right: 46px;
    bottom: 24px;
    text-align: right;
    color: var(--ink-light);
  }
  .contact__name {
    margin: 0;
    font-size: 30px;
    font-weight: 700;
    color: var(--brand-blue);
    line-height: 1;
  }
  .contact__role {
    margin: 2px 0 10px;
    font-size: 13px;
    font-weight: 600;
  }
  .contact__address {
    font-style: normal;
    font-size: 12px;
    line-height: 1.35;
    margin-bottom: 8px;
  }
  .contact__list {
    list-style: none;
    margin: 0;
    padding: 0;
    font-size: 12px;
    line-height: 1.45;
  }
  .contact__list li {
    display: flex;
    justify-content: flex-end;
    align-items: center;
    gap: 7px;
  }
  .contact__icon { width: 11px; height: 11px; fill: var(--brand-blue); flex: none; }
  .accent-bar {
    position: absolute;
    right: 0;
    top: 150px;
    width: 26px;
    height: 44px;
    background: var(--brand-blue);
  }

  /* Front side: brand */
  .card--front { background: var(--card-blue); }
  .card--front .wordmark {
    top: 50%;
    left: 50%;
    transform: translate(-50%, -50%);
    color: var(--brand-deep);
  }
  .card--front .wordmark__dot { width: 44px; height: 44px; }
  .card--front .wordmark__name { font-size: 40px; letter-spacing: 4px; }
  .card--front .wordmark__tag { font-size: 12px; letter-spacing: 1.8px; }
</style>
</head>
<body>
<main class="canvas">
  <section class="card card--back" aria-label="Business card, contact side">
    <div class="wordmark">
      <span class="wordmark__dot"></span>
      <span class="wordmark__text">
        <span class="wordmark__name">QUARROW</span>
        <span class="wordmark__tag">SIGNAL INSTRUMENTS</span>
      </span>
    </div>

    <div class="accent-bar"></div>

    <div class="contact">
      <h1 class="contact__name">Marlene</h1>
      <p class="contact__role">Director</p>
      <address class="contact__address">
        1180 Halden Ridge Road •<br>
        Alderford, CO 80642
      </address>
      <ul class="contact__list">
        <li>+001 555 218 4407
          <svg class="contact__icon" viewBox="0 0 24 24" aria-hidden="true"><path d="M6.6 10.8a15 15 0 0 0 6.6 6.6l2.2-2.2c.3-.3.7-.4 1-.2 1.1.4 2.3.6 3.6.6.6 0 1 .4 1 1V20c0 .6-.4 1-1 1A17 17 0 0 1 3 4c0-.6.4-1 1-1h3.5c.6 0 1 .4 1 1 0 1.3.2 2.5.6 3.6.1.3 0 .7-.2 1z"/></svg>
        </li>
        <li>+001 555 218 4493
          <svg class="contact__icon" viewBox="0 0 24 24" aria-hidden="true"><path d="M6 3h9v5h3a2 2 0 0 1 2 2v11H4V10a2 2 0 0 1 2-2zm2 2v3h5V5zm0 8v2h2v-2zm4 0v2h2v-2zm4 0v2h2v-2zm-8 4v2h2v-2zm4 0v2h2v-2zm4 0v2h2v-2z"/></svg>
        </li>
        <li>www.quarrowsignal.com
          <svg class="contact__icon" viewBox="0 0 24 24" aria-hidden="true"><path d="M12 2a10 10 0 1 0 0 20 10 10 0 0 0 0-20zm6.9 6h-3a15 15 0 0 0-1.3-3.9A8 8 0 0 1 18.9 8zM12 4c.8 1.2 1.5 2.5 1.9 4h-3.8c.4-1.5 1.1-2.8 1.9-4zM4.3 14a8 8 0 0 1 0-4h3.4a16 16 0 0 0 0 4zm.8 2h3a15 15 0 0 0 1.3 3.9A8 8 0 0 1 5.1 16zm3-8h-3a8 8 0 0 1 4.3-3.9A15 15 0 0 0 8.1 8zM12 20c-.8-1.2-1.5-2.5-1.9-4h3.8c-.4 1.5-1.1 2.8-1.9 4zm2.3-6H9.7a14 14 0 0 1 0-4h4.6a14 14 0 0 1 0 4zm.3 5.9c.6-1.2 1-2.5 1.3-3.9h3a8 8 0 0 1-4.3 3.9zm1.7-5.9a16 16 0 0 0 0-4h3.4a8 8 0 0 1 0 4z"/></svg>
        </li>
        <li>info@quarrowsignal.com
          <svg class="contact__icon" viewBox="0 0 24 24" aria-hidden="true"><path d="M3 5h18a1 1 0 0 1 1 1v12a1 1 0 0 1-1 1H3a1 1 0 0 1-1-1V6a1 1 0 0 1 1-1zm9 7.5L4.5 7v10h15V7z"/></svg>
        </li>
      </ul>
    </div>
  </section>

  <section class="card card--front" aria-label="Business card, brand side">
    <div class="wordmark">
      <span class="wordmark__dot"></span>
      <span class="wordmark__text">
        <span class="wordmark__name">QUARROW</span>
        <span class="wordmark__tag">SIGNAL INSTRUMENTS</span>
      </span>
    </div>
  </section>
</main>
</body>
</html>
```